Modern Business Card

Modern professional business card with more than just logo and demographic info. Something memorable.

We are a trendy/modern chiropractic group with an emphasis on neurology, hence the minimalist-type brain logo. We want to convey that modern and technical aspect with professionalism and the elite nature of our practice environment.

```html
<!DOCTYPE html>
<html lang="en">
<head>
<meta charset="utf-8">
<title>Northgate Spine – Business Card</title>
<link href="https://fonts.googleapis.com/css2?family=Montserrat:wght@400;500;700&display=swap" rel="stylesheet">
<style>
  :root {
    --brand-blue: #4a80c2;
    --brand-blue-light: #7ea6d8;
    --card-white: #ffffff;
    --ink: #1c1c1c;
    --ink-soft: #4a4a4a;
    --backdrop: #e9eaec;
  }
  * { box-sizing: border-box; margin: 0; padding: 0; }
  html, body {
    width: 1200px; height: 900px; overflow: hidden;
    background: var(--backdrop);
    font-family: "Montserrat", Arial, sans-serif;
  }
  .sheet {
    position: relative; width: 1200px; height: 900px;
  }
  .card {
    position: absolute; width: 640px; height: 366px;
    border-radius: 4px; overflow: hidden;
    box-shadow: 0 10px 28px rgba(0,0,0,0.12);
  }
  /* Front */
  .card-front {
    left: 180px; top: 44px;
    background: var(--brand-blue);
  }
  .front-decoration {
    position: absolute; left: 0; top: 0; width: 300px; height: 100%;
    background: linear-gradient(90deg, var(--card-white) 0%, var(--brand-blue-light) 55%, var(--brand-blue) 100%);
  }
  .front-brand {
    position: absolute; left: 330px; top: 150px;
    display: flex; align-items: center; gap: 14px;
  }
  .brand-dot {
    width: 34px; height: 34px; border-radius: 50%;
    background: var(--card-white);
  }
  .brand-name {
    font-weight: 700; font-size: 30px; letter-spacing: 2px;
    text-transform: uppercase; color: var(--card-white);
    line-height: 1;
  }
  /* Back */
  .card-back {
    left: 380px; top: 490px;
    background: var(--card-white);
  }
  .back-decoration {
    position: absolute; right: 0; top: 0; width: 250px; height: 200px;
    border-bottom-left-radius: 60px;
    background: linear-gradient(200deg, var(--brand-blue) 0%, var(--brand-blue-light) 70%, var(--card-white) 100%);
  }
  .back-brand {
    position: absolute; left: 42px; top: 44px;
    display: flex; align-items: center; gap: 10px;
  }
  .back-brand .brand-dot { width: 26px; height: 26px; background: var(--brand-blue); }
  .back-brand .brand-name { font-size: 22px; color: var(--ink); }
  .accent-bar {
    position: absolute; left: 0; top: 140px; width: 14px; height: 50px;
    background: var(--brand-blue);
  }
  .person { position: absolute; left: 42px; top: 132px; }
  .person-name {
    font-weight: 700; font-size: 24px; color: var(--brand-blue);
    letter-spacing: 0.5px; text-transform: uppercase;
  }
  .person-title { font-size: 15px; color: var(--ink-soft); margin-top: 2px; }
  .address {
    position: absolute; left: 42px; top: 200px;
    font-size: 14px; color: var(--ink-soft); line-height: 1.4;
  }
  .contacts {
    position: absolute; left: 42px; top: 254px;
    list-style: none; font-size: 14px; color: var(--ink-soft); line-height: 1.5;
  }
  .contacts li { display: flex; align-items: center; gap: 8px; }
  .contacts svg { width: 12px; height: 12px; fill: var(--brand-blue); flex: none; }
  .web-domain { color: var(--brand-blue); }
</style>
</head>
<body>
<main class="sheet">
  <section class="card card-front" aria-label="Card front">
    <div class="front-decoration" role="img" aria-label="Decorative pattern of rounded bars in white and blue"></div>
    <div class="front-brand">
      <span class="brand-dot"></span>
      <span class="brand-name">Northgate Spine</span>
    </div>
  </section>

  <section class="card card-back" aria-label="Card back">
    <div class="back-decoration" role="img" aria-label="Decorative pattern of blue rounded bars"></div>
    <div class="back-brand">
      <span class="brand-dot"></span>
      <span class="brand-name">Northgate Spine</span>
    </div>
    <div class="accent-bar"></div>
    <div class="person">
      <p class="person-name">Daniel Mercer</p>
      <p class="person-title">Senior Partner</p>
    </div>
    <p class="address">12 Keller Avenue Brookfield,<br>Riverton, 4410</p>
    <ul class="contacts">
      <li><svg viewBox="0 0 24 24"><path d="M6.6 10.8a15.1 15.1 0 0 0 6.6 6.6l2.2-2.2c.3-.3.7-.4 1-.2 1.1.4 2.3.6 3.6.6.6 0 1 .4 1 1V20c0 .6-.4 1-1 1A17 17 0 0 1 3 4c0-.6.4-1 1-1h3.5c.6 0 1 .4 1 1 0 1.3.2 2.5.6 3.6.1.3 0 .7-.2 1z"/></svg>+120 5555 0142</li>
      <li><svg viewBox="0 0 24 24"><path d="M7 1h10a2 2 0 0 1 2 2v18a2 2 0 0 1-2 2H7a2 2 0 0 1-2-2V3a2 2 0 0 1 2-2zm0 3v14h10V4zm5 15.5a1 1 0 1 0 0 2 1 1 0 0 0 0-2z"/></svg>+965 5555 0187</li>
      <li><svg viewBox="0 0 24 24"><path d="M2 5h20v14H2zm2 2v.5l8 5 8-5V7l-8 5z"/></svg>info@northgatespine.com</li>
      <li><svg viewBox="0 0 24 24"><circle cx="12" cy="12" r="10"/></svg>www.<span class="web-domain">northgatespine</span>.com</li>
    </ul>
  </section>
</main>
</body>
</html>
```